Fern Lattice Table & Chair Rentals

We need a business card for a table and chair rental company. We rent tables and chairs for weddings, funerals, business events and parties. We want something that looks clean and elegant while not being too busy. We would like colors in the green and blue hues and avoiding anything orange. We want to make sure the font is large enough to be seen easily.

Target Market(s)

Wedding & Event Rentals

Industry/Entity Type

Events

Contact Information for Business Card

Fern Lattice, sales@fernlatticerentals.com, fernlatticerentals.com, 360-555-0182

Requirements
Must have
• Easy to read font
Should not have
• Orange anywhere in the design

```html
<!DOCTYPE html>
<html lang="en">
<head>
<meta charset="utf-8">
<title>Fern Lattice Table &amp; Chair Rentals – Business Card</title>
<link rel="stylesheet" href="https://fonts.googleapis.com/css2?family=Roboto:wght@400;500&display=swap">
<style>
  :root {
    --bg: #e6e9e8;
    --card: #ffffff;
    --accent: #2f8f7a;
    --accent-dark: #1f6a8a;
    --ink: #151515;
    --muted: #444444;
    --rule: #9a9a9a;
  }
  * { margin: 0; padding: 0; box-sizing: border-box; }
  html, body { width: 1200px; height: 892px; overflow: hidden; background: var(--bg); }
  body { position: relative; font-family: "Roboto", Arial, sans-serif; color: var(--ink); }

  .card {
    position: absolute; left: 270px; width: 660px; height: 378px;
    background: var(--card); overflow: hidden;
    box-shadow: 0 2px 10px rgba(0,0,0,.18);
  }
  .card--back { top: 44px; }
  .card--front { top: 470px; }
  .card__shapes { position: absolute; inset: 0; width: 100%; height: 100%; }

  .brand { position: absolute; }
  .brand__name { font-weight: 500; letter-spacing: .5px; line-height: 1; }
  .brand__tagline { font-weight: 400; line-height: 1.2; margin-top: 6px; }

  .card--back .brand { left: 0; right: 0; top: 118px; text-align: center; }
  .card--back .brand__name { font-size: 60px; }
  .card--back .brand__tagline { font-size: 28px; margin-top: 10px; }

  .card--front .brand { left: 40px; top: 170px; }
  .card--front .brand__name { font-size: 36px; }
  .card--front .brand__tagline { font-size: 19px; }

  .company { position: absolute; right: 36px; top: 82px; text-align: right; }
  .company__name { font-size: 29px; font-weight: 400; }
  .company__hours { font-size: 12.5px; color: var(--muted); margin-top: 6px; }

  .contacts { position: absolute; right: 30px; top: 170px; list-style: none; }
  .contacts li {
    display: flex; justify-content: flex-end; align-items: center; gap: 12px;
    font-size: 17px; height: 26px;
  }
  .contacts .icon {
    width: 20px; height: 20px; border: 1.4px solid var(--ink); border-radius: 50%;
    display: flex; align-items: center; justify-content: center;
  }
  .contacts .icon svg { width: 11px; height: 11px; }
</style>
</head>
<body>

<section class="card card--back" aria-label="Card back">
  <svg class="card__shapes" viewBox="0 0 660 378" aria-hidden="true">
    <rect x="0" y="0" width="660" height="26" fill="var(--accent)"/>
    <polygon points="250,26 430,26 400,74 280,74" fill="var(--accent-dark)"/>
    <line x1="232" y1="26" x2="262" y2="74" stroke="var(--ink)" stroke-width="5"/>
    <line x1="448" y1="26" x2="418" y2="74" stroke="var(--ink)" stroke-width="5"/>
    <rect x="0" y="300" width="660" height="78" fill="var(--accent)"/>
    <polygon points="210,300 450,300 420,250 240,250" fill="var(--accent-dark)"/>
    <line x1="192" y1="300" x2="222" y2="250" stroke="var(--ink)" stroke-width="5"/>
    <line x1="468" y1="300" x2="438" y2="250" stroke="var(--ink)" stroke-width="5"/>
  </svg>
  <div class="brand">
    <p class="brand__name">Fern Lattice</p>
    <p class="brand__tagline">Table and Chair Rentals</p>
  </div>
</section>

<section class="card card--front" aria-label="Card front">
  <svg class="card__shapes" viewBox="0 0 660 378" aria-hidden="true">
    <rect x="0" y="0" width="660" height="26" fill="var(--accent)"/>
    <polygon points="230,26 410,26 440,62 200,62" fill="var(--accent-dark)"/>
    <line x1="212" y1="26" x2="182" y2="62" stroke="var(--ink)" stroke-width="5"/>
    <line x1="428" y1="26" x2="458" y2="62" stroke="var(--ink)" stroke-width="5"/>
    <line x1="40" y1="70" x2="624" y2="70" stroke="var(--rule)" stroke-width="1"/>
    <line x1="340" y1="152" x2="624" y2="152" stroke="var(--rule)" stroke-width="1"/>
    <line x1="380" y1="262" x2="624" y2="262" stroke="var(--rule)" stroke-width="1"/>
    <rect x="0" y="306" width="660" height="72" fill="var(--accent)"/>
    <polygon points="150,306 350,306 320,256 180,256" fill="var(--accent-dark)"/>
    <line x1="132" y1="306" x2="162" y2="256" stroke="var(--ink)" stroke-width="5"/>
    <line x1="368" y1="306" x2="338" y2="256" stroke="var(--ink)" stroke-width="5"/>
  </svg>

  <div class="brand">
    <p class="brand__name">Fern Lattice</p>
    <p class="brand__tagline">Table and Chair Rentals</p>
  </div>

  <div class="company">
    <p class="company__name">Fern Lattice Event Rentals, LLC</p>
    <p class="company__hours">Mon-Fri: 8am to 6pm - Saturday: 8am to 4pm - Sunday: 9am to 1pm</p>
  </div>

  <ul class="contacts">
    <li>360-555-0182
      <span class="icon"><svg viewBox="0 0 12 12"><path d="M2.5 1 L4.5 1 L5 3.5 L3.8 4.4 C4.4 5.8 6.2 7.6 7.6 8.2 L8.5 7 L11 7.5 L11 9.5 C11 10.4 10.3 11 9.5 11 C5 11 1 7 1 2.5 C1 1.7 1.6 1 2.5 1 Z" fill="var(--ink)"/></svg></span>
    </li>
    <li>www.fernlatticerentals.com
      <span class="icon"><svg viewBox="0 0 12 12"><rect x="1" y="1.5" width="10" height="7" rx="1" fill="none" stroke="var(--ink)" stroke-width="1.3"/><line x1="4" y1="11" x2="8" y2="11" stroke="var(--ink)" stroke-width="1.3"/><line x1="6" y1="8.5" x2="6" y2="11" stroke="var(--ink)" stroke-width="1.3"/></svg></span>
    </li>
    <li>sales@fernlatticerentals.com
      <span class="icon"><svg viewBox="0 0 12 12"><rect x="1" y="2.5" width="10" height="7" fill="var(--ink)"/><polyline points="1,2.5 6,6.5 11,2.5" fill="none" stroke="#fff" stroke-width="1"/></svg></span>
    </li>
  </ul>
</section>

</body>
</html>
```